Commercial Rooftop Solar business needs a website

We need a website with fantastic appeal for a new company based in Melbourne called Tallow Ridge Energy. We design and install solar energy systems for commercial applications across Australia. Our market is to focus on small to medium businesses looking for solar solutions, but we will also provide our service for residential customers. We would like a beautiful 'front page' feel to our home page, using photographs of solar PV systems and/or natural imagery. Our logo uses the colours orange and black, which could easily be echoed in photographic imagery of sunset and sunrise, for example. The design should communicate quiet confidence and professionalism to a corporate marketplace.

NEW POINTS FOR BRIEF: This design also needs to be flexible to allow for additional future content, including a Support page with sub pages, FAQ's, and a Blog.

As part of this design project, we will require the coding for the website to be completed by the designer.

We have seen some websites, which we like the look and feel of: these are listed below.

brightvanepower.com.au:

• Beautiful images underlaying brief text selling points.
• Simple ‘front cover’ style home page with elegant drop-down menu, stylish simple font style.
• Home page invites exploration through the menu links, rather than trying to provide all the information up front.
• Company logo and name in the top left hand corner, contact details accessible at top right hand, seems consistent in most sites.

kelpworks.com.au

rumbofield.com:
• Same element as the others is the front-page style home page with beautiful images underlying text.

We have a webpage that we started uploading content to. You can use some of the content there in your designs: www.tallowridgeenergy.com.au

Technical Specifications:
PAGES:

Home

About Us

Solutions - Commercial
- Residential

Products - Solar Panels - Vorla Heron, Vorla TELD, Vorla QB
- Solar Inverters - Kestamo, BrilQuill
- Monitoring systems - Dunmere Metrics
- Batteries - RW

- Datasheets have been provided for reference but if it's too much work, you can use generic text and we will provide content later.

Contact Us

FUTURE PAGES (Please consider in structure, where links could be placed):

Support

FAQ's

Blog.

We could provide some content for the Support page soon, but the Blog and FAQ's are future pages which we don't want highlighted in the design as we don't yet have content.

Phone: 1800 7 BIRCH
Email: sales@tallowridgeenergy.com.au

Currently, I do not have images and text available. Please
use placeholders in the meantime. The final text and images will be uploaded for the winner once a winning design has been selected.

Target Market(s)

Primary focus is on small to medium sized business owners. Those owners will have a house which may be suitable for solar so we want to cater to residential deeper in the website.

Industry/Entity Type

Solar Energy

Coding

Coded - Design and coding required

Number of Pages Required

5+ page

Colors
f78f20
0255a3

Requirements
Must have
• Logo as per attachments.
Nice to have
• Logo can have alternate colours Eg. White on Orange or Black etc. provided colour correct logo is shown somewhere eg. footer or contact page.
• In the active site, I'd like to have:
• Very slowly zooming images - barely perceptible.
• Title text that rolls into place
• Subtle movements
• See https://plumtally.com.au/ for example

```html
<!DOCTYPE html>
<html lang="en">
<head>
<meta charset="utf-8">
<title>Tallow Ridge Energy – Solutions</title>
<link rel="stylesheet" href="https://fonts.googleapis.com/css2?family=Lato:wght@400;700&family=Michroma&family=Poppins:wght@500;600&display=swap">
<style>
:root{
  --accent:#ff3d17;
  --ink:#1c1c1c;
  --body:#4a4a4a;
  --white:#ffffff;
  --footer:#161616;
  --footer-deep:#0b0b0b;
  --rule:#3a3a3a;
}
*{box-sizing:border-box;margin:0;padding:0}
html,body{width:846px;height:1200px;overflow:hidden;background:var(--white)}
body{position:relative;font-family:'Lato',sans-serif;color:var(--body)}

.hero{position:absolute;left:0;top:0;width:846px;height:321px;
  background:linear-gradient(180deg,#6d6f78 0%,#a2836a 22%,#e07a3c 40%,#c35a2c 52%,#4a3a3f 62%,#2b3550 80%,#1a2236 100%)}
.brand{position:absolute;left:112px;top:34px;width:110px;color:var(--white);
  font-family:'Michroma',sans-serif;font-size:11px;line-height:15px;text-align:center;letter-spacing:1px}
.topbar{position:absolute;right:106px;top:15px;display:flex;align-items:center;gap:12px}
.phone{display:flex;align-items:center;gap:6px;color:var(--white);font-family:'Lato',sans-serif;font-size:13px;font-weight:700}
.estimate{background:var(--accent);color:var(--white);font-size:9px;font-weight:700;padding:5px 12px;border-radius:12px;border:1px solid #fff6}
.nav{position:absolute;right:106px;top:58px;display:flex;gap:33px;font-family:'Michroma',sans-serif;font-size:8.5px;letter-spacing:1.6px;color:var(--white)}
.nav .active{color:var(--accent)}
.hero h1{position:absolute;left:0;width:846px;top:166px;text-align:center;color:var(--white);
  font-family:'Poppins',sans-serif;font-weight:600;font-size:19.5px;line-height:25px}

.section-title{position:absolute;top:352px;left:0;width:846px;display:flex;justify-content:center;align-items:center;gap:6px}
.section-title span{display:block;width:54px;height:1px;background:var(--ink)}
.section-title h2{font-family:'Michroma',sans-serif;font-weight:400;font-size:20px;letter-spacing:3px;color:var(--ink)}

.photo{position:absolute}
.photo.commercial{left:0;top:424px;width:430px;height:278px;background:linear-gradient(135deg,#3b78c9,#8ab8e8 45%,#2f5f8c)}
.photo.residential{left:430px;top:702px;width:416px;height:277px;background:linear-gradient(180deg,#4a8fd8 0%,#9dbfe0 45%,#e8e8ea 60%,#6d9a4a 85%,#4d7d33)}
.notch{position:absolute;width:0;height:0;border-top:16px solid transparent;border-bottom:16px solid transparent}
.commercial .notch{right:0;top:36px;border-right:20px solid var(--white)}
.residential .notch{left:0;top:36px;border-left:20px solid var(--white)}

.solution{position:absolute;width:296px}
.solution.c{left:446px;top:426px}
.solution.r{left:116px;top:726px}
.solution h3{display:flex;align-items:center;gap:10px;font-family:'Michroma',sans-serif;font-weight:400;font-size:14.5px;letter-spacing:2px;color:var(--ink);margin-bottom:10px}
.solution p{font-size:8.3px;line-height:15.4px;margin-bottom:4px}

.footer{position:absolute;left:0;top:1009px;width:846px;height:161px;background:var(--footer);color:#ddd}
.col{position:absolute;top:20px}
.col h4{font-family:'Michroma',sans-serif;font-weight:400;font-size:9px;letter-spacing:1.6px;color:var(--white);padding-bottom:8px;border-bottom:1px dotted #555;margin-bottom:10px}
.links{left:113px;width:75px}
.links li{list-style:none;font-size:8px;line-height:22.4px}
.links li::before{content:"› ";color:#777}
.inquiry{left:254px;width:135px}
.field{background:var(--white);color:#666;font-size:6.5px;padding:3px 3px;height:14px;margin-bottom:4px;border-radius:2px}
.field.msg{height:24px}
.submit{display:inline-block;background:var(--accent);color:var(--white);font-family:'Michroma',sans-serif;font-size:6px;padding:4px 11px;border-radius:8px;margin-top:2px}
.contact{left:426px;width:140px}
.contact .row{display:flex;gap:6px;font-size:8.5px;color:var(--white);padding:4px 0 7px;border-bottom:1px dotted #444}
.contact .row:last-child{border:none}
.contact strong{font-size:10px;display:block}
.contact small{font-size:7.5px;line-height:10.5px;display:block}
.divider{position:absolute;top:20px;width:1px;height:120px;background:var(--rule)}
.footer-brand{position:absolute;left:620px;top:64px;width:120px;display:flex;align-items:center;gap:8px;color:#c9c9c9;font-family:'Michroma',sans-serif;font-size:10px;line-height:14px}
.footer-brand i{width:14px;height:14px;border-radius:50%;background:#c9c9c9;flex:none}
.copyright{position:absolute;left:0;top:1170px;width:846px;height:30px;background:var(--footer-deep);color:#bbb;font-size:7.5px;text-align:center;line-height:30px}
</style>
</head>
<body>

<header class="hero" role="img" aria-label="Sunset sky over a field of solar panels">
  <div class="brand">TALLOW RIDGE ENERGY</div>
  <div class="topbar">
    <div class="phone">
      <svg width="20" height="20" viewBox="0 0 20 20"><circle cx="10" cy="10" r="9" fill="none" stroke="#fff" stroke-width="1.3"/><path d="M7 5.5l1.6 2.2-1 1.1c.6 1.3 1.5 2.2 2.6 2.7l1.1-1 2.2 1.6-.9 1.6c-3.4-.4-6.3-3.4-6.6-6.8z" fill="#fff"/></svg>
      1800 7 BIRCH
    </div>
    <div class="estimate">FREE ESTIMATE</div>
  </div>
  <nav class="nav"><span>HOME</span><span>ABOUT US</span><span class="active">SOLUTIONS</span><span>CONTACT US</span></nav>
  <h1>Tallow Ridge Energy Is A National Company That<br>Specialises In Solar Solutions For The Commercial<br>And Residential</h1>
</header>

<div class="section-title"><span></span><h2>OUR SOLUTIONS</h2><span></span></div>

<div class="photo commercial" role="img" aria-label="Glass office towers against a blue sky"><div class="notch"></div></div>
<section class="solution c">
  <h3><svg width="22" height="22" viewBox="0 0 22 22"><rect x="2" y="3" width="10" height="18" fill="#333"/><rect x="12" y="8" width="8" height="13" fill="#333"/><g fill="#fff"><rect x="4" y="6" width="2" height="2"/><rect x="8" y="6" width="2" height="2"/><rect x="4" y="11" width="2" height="2"/><rect x="8" y="11" width="2" height="2"/><rect x="14" y="11" width="2" height="2"/><rect x="14" y="15" width="2" height="2"/><rect x="6" y="16" width="2" height="5"/></g></svg>COMMERCIAL</h3>
  <p>Aenean id orci elementum, interdum diam in, viverra ipsum. Fusce molestie, turpis eget elementum imperdiet, sem mi ultricies quam, ut condimentum mi arcu vel ligula. Ut nec auctor libero, eu blandit augue. Curabitur et ipsum eros. Curabitur sit amet leo ut magna fringilla sagittis. Etiam tempus elit sapien, laoreet condimentum ligula suscipit at. Phasellus elementum id felis in molestie. Proin ac massa ullamcorper, euismod dolor et, suscipit ante. Pellentesque congue velit non vestibulum fermentum. Fusce pulvinar imperdiet eros, ac vulputate ipsum iaculis in. Sed at arcu orci. Cras fermentum felis eget magna dictum suscipit.</p>
  <p>Ut porta eu quam nec aliquam. Maecenas sit amet elit lacinia, volutpat dui non, pretium odio. Donec vel augue sed augue sollicitudin tempor. Suspendisse magna sem, consequat et neque ut, aliquam sagittis enim. Etiam quis dictum orci. Nunc malesuada, eros nec imperdiet eleifend, leo sapien viverra dolor, eu iaculis quam odio ac justo.</p>
</section>

<section class="solution r">
  <h3><svg width="22" height="22" viewBox="0 0 22 22"><path d="M11 2L1 9h3v12h14V9h3z" fill="#333"/><g fill="#fff"><rect x="6" y="11" width="3" height="3"/><rect x="13" y="11" width="3" height="3"/><rect x="9.5" y="16" width="3" height="5"/></g></svg>RESIDENTIAL</h3>
  <p>Aenean id orci elementum, interdum diam in, viverra ipsum. Fusce molestie, turpis eget elementum imperdiet, sem mi ultricies quam, ut condimentum mi arcu vel ligula. Ut nec auctor libero, eu blandit augue. Curabitur et ipsum eros. Curabitur sit amet leo ut magna fringilla sagittis. Etiam tempus elit sapien, laoreet condimentum ligula suscipit at. Phasellus elementum id felis in molestie. Proin ac massa ullamcorper, euismod dolor et, suscipit ante. Pellentesque congue velit non vestibulum fermentum. Fusce pulvinar imperdiet eros, ac vulputate ipsum iaculis in. Sed at arcu orci. Cras fermentum felis eget magna dictum suscipit.</p>
  <p>Ut porta eu quam nec aliquam. Maecenas sit amet elit lacinia, volutpat dui non, pretium odio. Donec vel augue sed augue sollicitudin tempor. Suspendisse magna sem, consequat et neque ut, aliquam sagittis enim. Etiam quis dictum orci. Nunc malesuada, eros nec imperdiet eleifend, leo sapien viverra dolor, eu iaculis quam odio ac justo.</p>
</section>
<div class="photo residential" role="img" aria-label="White two-storey family house with a green lawn"><div class="notch"></div></div>

<footer class="footer">
  <div class="col links"><h4>QUICK LINKS</h4><ul><li>Home</li><li>About Us</li><li>Solutions</li><li>Contact Us</li></ul></div>
  <div class="divider" style="left:221px"></div>
  <div class="col inquiry"><h4>QUICK INQUIRY</h4>
    <div class="field">Name</div><div class="field">Email</div><div class="field msg">Message</div>
    <span class="submit">SUBMIT</span>
  </div>
  <div class="divider" style="left:405px"></div>
  <div class="col contact"><h4>CONTACT DETAILS</h4>
    <div class="row"><svg width="8" height="10" viewBox="0 0 8 10"><path d="M4 0a4 4 0 0 0-4 4c0 3 4 6 4 6s4-3 4-6a4 4 0 0 0-4-4z" fill="#ff3d17"/><circle cx="4" cy="4" r="1.4" fill="#161616"/></svg><div><strong>TALLOW RIDGE ENERGY</strong><small>123 euismod cidun ut aoreetmok laoreet dol magnak aliquam</small></div></div>
    <div class="row"><svg width="9" height="9" viewBox="0 0 9 9"><path d="M1 .5l2 2.3-1 1c.6 1.3 1.4 2.1 2.7 2.7l1-1L8 7.5 7 9C3.5 8.6.4 5.5 0 2z" fill="#ff3d17"/></svg>1800 7 BIRCH</div>
    <div class="row"><svg width="9" height="7" viewBox="0 0 9 7"><rect width="9" height="7" fill="#ff3d17"/><path d="M0 0l4.5 4L9 0" fill="none" stroke="#161616" stroke-width=".8"/></svg>info@tallowridgeenergy.com.au</div>
  </div>
  <div class="divider" style="left:598px"></div>
  <div class="footer-brand"><i></i>TALLOW RIDGE ENERGY</div>
</footer>
<div class="copyright">Copyright © 2017 Tallow Ridge Energy. All Right Reserved.</div>

</body>
</html>
```